Motor Oil Lubricant Package Labels

We are looking for a logo and label that we can put on our motor oil bottle 1 liter and 5 liter. The name of our motor oil is Corvana. We want to design our flagship logo for CORVANA MOTOR OILS and as well as the label that will go on the bottle. We have some drafts that we have come up with attached and would like to see more options. The concept of a timeless motor oil and the endless loop of lubricating oils incorporated in the design. We will have full synthetic motor oil, a synthetic blend motor, ATF III transmission fluid, KRL-VI transmission fluid. hydraulic oils etc. Examples will be attached
Target Market(s)
Automotive Lubricants and Chemicals
Industry/Entity Type
Automotive
Logo Text
Corvana Lubricants
Font styles to use
Other font styles liked:
- Let designer choose
Requirements
Must have
- The Corvana sign incorporated in a very cool way to our name. Our brand needs to stick out
Nice to have
- Automotive lubricant related and colors red, white, and blue incorporated in the design
Should not have
- Images of individuals and or topics not related to automotive lubricants.

```html
<!DOCTYPE html>
<html lang="en">
<head>
<meta charset="utf-8">
<title>Corvana Lubricants – ATF III Label</title>
<link rel="stylesheet" href="https://fonts.googleapis.com/css2?family=Oswald:wght@400;500;700&family=Roboto+Condensed:wght@400;700&family=Russo+One&display=swap">
<style>
  :root {
    --paper: #ffffff;
    --label-dark: #262626;
    --brand-red: #e3202a;
    --brand-green: #129a45;
    --text-light: #f2f2f2;
    --ink: #111111;
  }
  html, body { margin: 0; padding: 0; overflow: hidden; background: var(--paper); }
  .canvas { display: block; width: 1200px; height: 851px; }
  .brand-name { font-family: "Oswald", sans-serif; font-weight: 700; fill: var(--text-light); letter-spacing: 2px; }
  .brand-sub { font-family: "Oswald", sans-serif; font-weight: 700; fill: var(--text-light); letter-spacing: 2px; }
  .tag { font-family: "Russo One", sans-serif; }
  .tag-green { fill: var(--brand-green); }
  .tag-white { fill: var(--text-light); }
  .product-big { font-family: "Oswald", sans-serif; font-weight: 700; fill: var(--brand-green); }
  .product-sub { font-family: "Oswald", sans-serif; font-weight: 700; fill: var(--brand-red); }
  .product-sub-light { font-family: "Oswald", sans-serif; font-weight: 500; fill: var(--text-light); }
  .caption { font-family: "Russo One", sans-serif; fill: var(--text-light); }
  .volume { font-family: "Oswald", sans-serif; font-weight: 700; fill: var(--text-light); }
  .body { font-family: "Roboto Condensed", sans-serif; fill: var(--text-light); }
  .body-strong { font-weight: 700; }
  .accent-red { fill: var(--brand-red); font-weight: 700; }
  .accent-green { fill: var(--brand-green); font-weight: 700; }
  .bullet { font-family: "Oswald", sans-serif; font-weight: 500; fill: var(--brand-red); }
  .sus { font-family: "Oswald", sans-serif; font-weight: 700; fill: var(--text-light); }
  .made-strip { font-family: "Roboto Condensed", sans-serif; font-weight: 700; fill: var(--ink); }
</style>
</head>
<body>
<svg class="canvas" viewBox="0 0 1468 1041" xmlns="http://www.w3.org/2000/svg">
  <defs>
    <linearGradient id="brushed" x1="0" y1="0" x2="1" y2="1">
      <stop offset="0" stop-color="#303030"/>
      <stop offset="0.5" stop-color="#1f1f1f"/>
      <stop offset="1" stop-color="#2c2c2c"/>
    </linearGradient>
    <radialGradient id="seal" cx="0.4" cy="0.35" r="0.7">
      <stop offset="0" stop-color="#f0cf7a"/>
      <stop offset="1" stop-color="#b07d22"/>
    </radialGradient>
    <linearGradient id="flag" x1="0" y1="0" x2="1" y2="1">
      <stop offset="0" stop-color="#2b3f8f"/>
      <stop offset="0.45" stop-color="#d23a3a"/>
      <stop offset="1" stop-color="#f1d6d6"/>
    </linearGradient>
    <clipPath id="front-clip"><rect x="127" y="60" width="573" height="928" rx="35"/></clipPath>
    <clipPath id="back-clip"><rect x="767" y="60" width="573" height="928" rx="35"/></clipPath>
  </defs>

  <g class="label-front" clip-path="url(#front-clip)">
    <rect x="127" y="60" width="573" height="928" fill="url(#brushed)"/>
    <path d="M240,60 C400,60 560,100 700,190 L700,150 C600,90 480,62 440,60 Z" fill="var(--brand-red)"/>
    <path d="M440,60 L700,60 L700,150 C600,90 520,62 440,60 Z" fill="var(--paper)"/>
    <path d="M700,178 C560,260 440,420 430,560 C420,700 360,860 318,988 L380,988 C430,860 470,720 480,600 C490,430 600,262 700,202 Z" fill="var(--brand-red)"/>
    <path d="M700,202 C600,262 490,430 480,600 C470,720 440,840 400,930 C520,900 620,880 700,860 Z" fill="var(--paper)"/>
    <path d="M400,930 C520,900 620,880 700,860 L700,988 L380,988 Z" fill="var(--brand-red)"/>

    <text class="brand-name" x="172" y="297" font-size="86" textLength="384" lengthAdjust="spacingAndGlyphs">CORVANA</text>
    <text class="brand-sub" x="540" y="333" font-size="22" text-anchor="end">LUBRICANTS</text>

    <rect x="224" y="390" width="240" height="32" fill="var(--paper)" opacity="0.92"/>
    <text class="tag tag-green" x="344" y="415" font-size="24" text-anchor="middle">MOST ADVANCED</text>
    <rect x="238" y="423" width="210" height="30" fill="var(--brand-red)"/>
    <text class="tag tag-white" x="343" y="446" font-size="22" text-anchor="middle">PERFORMANCE</text>
    <text class="caption" x="343" y="479" font-size="14" text-anchor="middle">MAXIMUM PROTECTION</text>
    <text class="caption" x="343" y="499" font-size="14" text-anchor="middle">FOR MORE MILES</text>

    <text class="product-big" transform="translate(578,470) rotate(90)" font-size="112" textLength="330" lengthAdjust="spacingAndGlyphs">ATF III</text>
    <text class="product-sub" transform="translate(514,550) rotate(90)" font-size="54" textLength="248" lengthAdjust="spacingAndGlyphs">KRL/MRV</text>

    <circle cx="222" cy="735" r="62" fill="url(#seal)" role="img" aria-label="Certification seal"/>

    <text class="volume" x="170" y="947" font-size="30">32oz 1946mL</text>
    <text class="volume" x="463" y="943" font-size="24" text-anchor="middle">Made In USA</text>
    <text class="volume" x="510" y="958" font-size="12" text-anchor="middle">★ ★ ★</text>
  </g>

  <g class="label-back" clip-path="url(#back-clip)">
    <rect x="767" y="60" width="573" height="928" fill="url(#brushed)"/>
    <path d="M960,60 C1120,62 1250,100 1340,175 L1340,130 C1270,85 1180,62 1110,60 Z" fill="var(--brand-red)"/>
    <path d="M1110,60 L1340,60 L1340,130 C1270,85 1180,62 1110,60 Z" fill="var(--paper)"/>

    <text class="brand-name" x="797" y="146" font-size="48" textLength="208" lengthAdjust="spacingAndGlyphs">CORVANA</text>
    <text class="brand-sub" x="997" y="166" font-size="14" text-anchor="end">LUBRICANTS</text>

    <circle cx="1244" cy="172" r="62" fill="url(#seal)" role="img" aria-label="Certification seal"/>

    <text class="product-big" x="838" y="220" font-size="54" textLength="132" lengthAdjust="spacingAndGlyphs">ATF III</text>
    <text class="product-sub-light" x="919" y="247" font-size="22" text-anchor="middle">KRL/MRV</text>

    <rect x="1005" y="195" width="150" height="20" fill="var(--paper)" opacity="0.92"/>
    <text class="tag tag-green" x="1080" y="211" font-size="15" text-anchor="middle">MOST ADVANCED</text>
    <rect x="1013" y="216" width="140" height="20" fill="var(--brand-red)"/>
    <text class="tag tag-white" x="1083" y="232" font-size="15" text-anchor="middle">PERFORMANCE</text>

    <g class="body" font-size="19">
      <text x="788" y="276" textLength="532" lengthAdjust="spacing"><tspan class="accent-red">CORVANA LUBRICANTS</tspan> <tspan class="accent-green">15W30</tspan> <tspan class="accent-red">and</tspan> <tspan class="accent-green">ATF</tspan> <tspan class="body-strong">Heavy Duty Diesel Motor</tspan></text>
      <text x="788" y="301" textLength="532" lengthAdjust="spacing" class="body-strong">Oil provides the ultimate performance and protection, especially</text>
      <text x="788" y="326" textLength="532" lengthAdjust="spacing"><tspan class="body-strong">under severe driving conditions.</tspan> It utilized newly developed additive</text>
      <text x="788" y="351" textLength="532" lengthAdjust="spacing">technology to achieve among the lowest rates of wear ever for motor</text>
      <text x="788" y="376" textLength="532" lengthAdjust="spacing">oils, well exceeding the most stringent North American specifications</text>
      <text x="788" y="401" textLength="532" lengthAdjust="spacing">for wear control, cleanliness and sludge, oxidation control, and</text>
      <text x="788" y="426" textLength="532" lengthAdjust="spacing">emission system and seal compatibility, while meeting the standards</text>
      <text x="788" y="451">for fuel economy.</text>
      <text x="788" y="477" textLength="532" lengthAdjust="spacing"><tspan class="accent-red">Licensed NLC GF-5 and NLC SN</tspan> “Resource Conserving” by the</text>
      <text x="788" y="502" textLength="532" lengthAdjust="spacing">National Lubricant Council (NLC) as all previous service</text>
      <text x="788" y="527" textLength="530" lengthAdjust="spacing">classification. It is compatible with all conventional and synthetic oils.</text>
    </g>

    <g class="bullet" font-size="19">
      <text x="788" y="552">•</text><text x="840" y="552">Provides Protections That Conventional Oils Can’t</text>
      <text x="788" y="577">•</text><text x="838" y="577">Won’t Break Down Under Extreme Temperature</text>
      <text x="788" y="602">•</text><text x="838" y="602">Superior Protection For Extended Service Intervals.</text>
    </g>

    <g class="body" font-size="15">
      <text x="788" y="638" textLength="397" lengthAdjust="spacing"><tspan class="accent-red">CORVANA MOTOR OIL</tspan> is manufactured to stringent standards.</text>
      <text x="788" y="658" textLength="397" lengthAdjust="spacing">Every batch is tested, from raw materials to finished product, to</text>
      <text x="788" y="678" textLength="397" lengthAdjust="spacing">insure you’re getting the Best Protection and Highest</text>
      <text x="788" y="698">Performance from every quart.</text>

      <text x="788" y="738" class="accent-red" textLength="397" lengthAdjust="spacing">WARNING! AVOID SKIN CONTACT WITH USED MOTOR OIL!</text>
      <text x="788" y="758" textLength="397" lengthAdjust="spacing">Used motor oils have caused skin cancer in laboratory animals</text>
      <text x="788" y="778" textLength="397" lengthAdjust="spacing">when repeatedly applied and left in place between applications.</text>
      <text x="788" y="798" textLength="397" lengthAdjust="spacing">In case of skin contact promptly wash thoroughly with soap and</text>
      <text x="788" y="818">water. Oil soiled clothing should be cleaned before reuse</text>

      <text x="788" y="858">DON’T POLLUTE! Conserve resources</text>
      <text x="788" y="878">Take used oil to collection center.</text>
    </g>

    <circle cx="1131" cy="918" r="45" fill="var(--paper)" role="img" aria-label="Service symbol"/>

    <text class="sus" x="1259" y="645" font-size="28" text-anchor="middle">SUS 350</text>
    <rect x="1199" y="653" width="120" height="213" fill="var(--paper)"/>
    <rect x="1199" y="873" width="120" height="67" fill="url(#flag)" role="img" aria-label="National flag"/>
    <rect x="1199" y="940" width="120" height="19" fill="var(--paper)"/>
    <text class="made-strip" x="1259" y="955" font-size="16" text-anchor="middle">MADE IN USA</text>
  </g>
</svg>
</body>
</html>
```